Bluefern Business Services needs a new interactive and interesting website

We need an interesting, professional, modern and functional company website for Bluefern Business Services - a young IT Services company based out of Chennai, India.

Bluefern Business Services is a fully owned subsidiary of Marlow Goods, one of the world's leading direct to consumer wine merchant.

We already have a registered company logo which must feature in the website.

We conceive, design, develop, test, implement and support IT solutions across the entire Marlow Goods IT landscape. For ex : We currently run about 25 e-commerce websites for Marlow Goods on ATG and Dot Net.

We would like to see our corporate colors used in the website. (Burgundy wine and wine green - source: www.bluefernbs-site.com)

We are looking at this website to communicate a fun, friendly and professionally managed company - reaching out to career seekers, prospective customers and general public.

For reference - The company name 'Bluefern' is an inspiration from the Marlow Goods lineage.

The second image with the world map is stickered on our main entrance to the office, I am not sure where this can be used -just putting it out there..

Please note that there are only a few more days to submit designs for this contest  !

I would appreciate if you can help posting your designs in time for our review and consideration.

Thanks.

Reason: Thanks for your inputs. We have a number of designers and a lot to digest and work with in the past few days. There has been a rush of new designs in the last few days Hence we will require more time to process these and make our decision. Hence i am requesting the contest to be open for more days. Regards, Tarun

Target Market(s)

Prospective job seekers who want to know more about the company and also wish to apply for a job vacancy
People wanting to know more about the company in general and our progress
People who want to see what we offer and how we can help them too - prospective customers
Companies that are interested in our IT Captive journey and are looking for a business opportunity

Industry/Entity Type

E-Commerce

Requirements
Must have
• Log In/ Register facility acting as a Single Sign on for Intranet (Employees)

Facility to post job vacancies (with an expiry date) and enable people to apply for a role and upload their CV/Resume.

Facility to Review Job applications

Facility for website visitors to contact Bluefern business Services via an online 'Contact Us' form with a split of job seekers and business opportunities

Gallery facility to upload pictures regarding company events
Nice to have
• Less Cluttered and contemporary design
Some Wine/Vineyard inspirations will be good but not too much, the company is an IT services company

```html
<!DOCTYPE html>
<html lang="en">
<head>
<meta charset="utf-8">
<title>Bluefern Business Services</title>
<link href="https://fonts.googleapis.com/css2?family=Open+Sans:wght@300;400;600;700&display=swap" rel="stylesheet">
<style>
:root{
  --burgundy:#8c0046;
  --burgundy-deep:#7a0f2e;
  --green:#3d9a16;
  --text:#666;
  --text-dark:#444;
  --rule:#dcdcdc;
  --white:#fff;
}
*{margin:0;padding:0;box-sizing:border-box}
html,body{width:922px;height:1200px;overflow:hidden;background:var(--white)}
body{font-family:'Open Sans',Arial,sans-serif;color:var(--text);position:relative}
a{text-decoration:none;color:inherit}
.abs{position:absolute}

.hero{left:0;top:0;width:922px;height:427px;
  background:
   radial-gradient(ellipse at 30% 25%,#f6f1d8 0%,rgba(240,230,190,.6) 22%,rgba(0,0,0,0) 50%),
   linear-gradient(180deg,#b7b28a 0%,#c9b878 35%,#9a8a3e 65%,#6e6a2c 100%);}
.hero-band{left:0;top:255px;width:922px;height:172px}
.hero-text{left:93px;top:286px;color:var(--white)}
.hero-text .kicker{font-size:27px;font-weight:400;line-height:34px}
.hero-text .headline{font-size:35px;font-weight:400;line-height:46px}
.hero-text .sub{font-size:20px;line-height:28px}
.slider-dots{left:880px;top:176px;display:flex;flex-direction:column;gap:15px}
.slider-dots span{width:12px;height:12px;border-radius:50%;background:rgba(255,255,255,.45)}
.slider-dots span.active{background:var(--white);border:3px solid var(--burgundy)}

.masthead{left:64px;top:0;width:793px;height:92px;background:var(--burgundy)}
.brand{left:29px;top:22px;color:var(--white);display:flex;gap:6px;align-items:flex-start}
.brand-mark{width:20px;height:20px;border-radius:50%;background:var(--white);margin-top:8px}
.brand-name{font-size:28px;font-weight:700;line-height:30px;letter-spacing:-.5px}
.brand-sub{font-size:16px;line-height:18px;margin-left:2px}
.masthead .divider{left:269px;top:19px;width:1px;height:53px;background:rgba(255,255,255,.7)}
.main-nav{right:22px;top:36px;display:flex;gap:27px;color:var(--white);font-size:14px}

h2.welcome{left:92px;top:462px;font-size:28px;font-weight:300;color:var(--green)}
.col-rule{left:461px;top:495px;width:1px;height:588px;background:var(--rule)}
.section-title{display:flex;align-items:center;gap:9px;color:var(--burgundy);font-size:18px;font-weight:400}
.section-title svg{flex:none}
.body-copy{font-size:13.4px;line-height:15.6px;text-align:justify;color:var(--text)}
.more-rule{width:328px;height:36px}

.latest .date{font-size:13px;color:var(--text);margin-bottom:6px}
.latest .title{font-size:13.4px;font-weight:700;color:var(--text-dark);line-height:16px}
.latest .desc{font-size:13.4px;line-height:16px;color:var(--text)}
.latest .read-more{display:block;text-align:right;font-size:10.5px;color:var(--green);margin:7px 13px 0 0}
.h-rule{height:1px;background:var(--rule);width:369px;left:461px}

.client-row{left:502px;top:808px;width:328px;display:flex;justify-content:space-between;align-items:center}
.client{display:flex;align-items:center;gap:5px;color:var(--burgundy);font-size:12px;font-weight:600}
.client .dot{width:9px;height:9px;border-radius:50%;background:var(--burgundy)}
.client .sq{width:9px;height:9px;background:var(--burgundy)}

.event-photo{top:960px;width:142px;height:94px}
.social{left:93px;top:1042px;display:flex;gap:10px}
.social a{display:flex;align-items:center;gap:4px;font-size:11px;color:#6a6a6a}
.social a span{width:25px;height:25px;background:#6a6a6a;display:block}

.site-footer{left:0;top:1120px;width:922px;height:80px;background:var(--burgundy);color:var(--white);text-align:center}
.footer-nav{display:flex;justify-content:center;gap:20px;font-size:11.5px;padding-top:14px}
.copyright{font-size:9px;margin-top:11px}
</style>
</head>
<body>

<div class="abs hero" role="img" aria-label="Sunlit vineyard rows at golden hour"></div>
<svg class="abs hero-band" viewBox="0 0 922 172" width="922" height="172" aria-hidden="true">
  <defs><linearGradient id="band" x1="0" x2="1"><stop offset="0" stop-color="#7f0a2c" stop-opacity=".92"/><stop offset="1" stop-color="#8c1030" stop-opacity=".85"/></linearGradient></defs>
  <polygon points="0,0 616,0 540,172 0,172" fill="url(#band)"/>
</svg>
<div class="abs hero-text">
  <div class="kicker">Lorem ipsum dolor sit amet</div>
  <div class="headline">CONSECTETUR ADIPISCING</div>
  <div class="sub">Phasellus luctus quis ipsum sed malesuada.</div>
</div>
<div class="abs slider-dots"><span class="active"></span><span></span><span></span><span></span></div>

<header class="abs masthead">
  <div class="abs brand">
    <div class="brand-mark"></div>
    <div><div class="brand-name">bluefern</div><div class="brand-sub">Business Services</div></div>
  </div>
  <div class="abs divider"></div>
  <nav class="abs main-nav"><a>Home</a><a>About us</a><a>Clients</a><a>Services</a><a>Careers</a><a>Contact us</a></nav>
</header>

<h2 class="abs welcome">Welcome</h2>
<div class="abs col-rule"></div>

<section class="abs" style="left:92px;top:513px;width:330px">
  <h3 class="section-title">
    <svg width="31" height="28" viewBox="0 0 31 28"><rect x="3" y="2" width="25" height="18" fill="none" stroke="#8c0046" stroke-width="2"/><rect x="0" y="22" width="31" height="4" fill="#8c0046"/><circle cx="15.5" cy="10" r="4" fill="none" stroke="#8c0046" stroke-width="1.6"/><line x1="15.5" y1="12" x2="15.5" y2="17" stroke="#8c0046" stroke-width="1.6"/></svg>
    Delivering IT Excellence
  </h3>
  <p class="body-copy" style="margin-top:17px">Welcome to Bluefern Business Services, an emerging provider of global IT consulting and software services. We are part of the Marlow Goods group, a family run business and the world's largest multi-channel home delivery wine merchant...</p>
</section>
<svg class="abs more-rule" style="left:92px;top:655px" viewBox="0 0 328 36"><line x1="0" y1="18" x2="284" y2="18" stroke="#dcdcdc"/><line x1="306" y1="0" x2="306" y2="36" stroke="#3d9a16"/><line x1="289" y1="18" x2="324" y2="18" stroke="#3d9a16"/></svg>

<section class="abs" style="left:92px;top:708px;width:330px">
  <h3 class="section-title">
    <svg width="22" height="22" viewBox="0 0 22 22"><path d="M3 19 L14 8" stroke="#8c0046" stroke-width="4" stroke-linecap="round"/><path d="M5 3 L19 17" stroke="#8c0046" stroke-width="3"/><circle cx="16" cy="5" r="4" fill="#8c0046"/><circle cx="4" cy="4" r="3" fill="#8c0046"/></svg>
    Services
  </h3>
  <ul style="list-style:none;margin-top:13px;font-size:13.4px;line-height:21.6px;color:var(--green)">
    <li>Packaged Applications</li><li>Enterprise Application Integration</li><li>Digital Commerce</li><li>Application Development &amp; Maintenance</li>
  </ul>
  <p class="body-copy" style="margin-top:15px;padding-left:1px">The services we provide enable the businesses we support to efficiently manage key functions, including order management (encompassing e-commerce websites, inbound and outbound call centre operations), order fulfilment, procurement, planning &amp; forecasting, warehouse management operations, financial management, global compliance and risk...</p>
</section>
<svg class="abs more-rule" style="left:92px;top:989px" viewBox="0 0 328 36"><line x1="0" y1="18" x2="284" y2="18" stroke="#dcdcdc"/><line x1="306" y1="0" x2="306" y2="36" stroke="#3d9a16"/><line x1="289" y1="18" x2="324" y2="18" stroke="#3d9a16"/></svg>

<div class="abs social"><a><span></span>Chirp</a><a><span></span>Netlink</a></div>

<section class="abs latest" style="left:502px;top:502px;width:328px">
  <h3 class="section-title">
    <svg width="24" height="22" viewBox="0 0 24 22"><rect x="0" y="5" width="24" height="17" fill="#8c0046"/><rect x="8" y="1" width="8" height="5" fill="none" stroke="#8c0046" stroke-width="2"/><line x1="0" y1="12" x2="24" y2="12" stroke="#fff"/></svg>
    Latest opportunities
  </h3>
  <div style="margin-top:8px">
    <div class="date">26/11/2013</div>
    <div class="title">Software Developers/Programmer Analysts - AX</div>
    <div class="desc">We are looking for a AX Software Developer to join...</div>
    <a class="read-more">read more &gt;&gt;</a>
  </div>
  <div style="margin-top:16px">
    <div class="date">26/11/2013</div>
    <div class="title">Software Developers/Programmer Analysts - AX</div>
    <div class="desc">We are looking for a AX Software Developer to join...</div>
    <a class="read-more">read more &gt;&gt;</a>
  </div>
</section>

<div class="abs h-rule" style="top:738px"></div>

<h3 class="abs section-title" style="left:502px;top:774px">
  <svg width="24" height="22" viewBox="0 0 24 22"><circle cx="9" cy="6" r="5" fill="#8c0046"/><path d="M0 22 Q9 9 18 22Z" fill="#8c0046"/><circle cx="17" cy="9" r="4" fill="#8c0046"/><path d="M12 22 Q18 13 24 22Z" fill="#8c0046"/></svg>
  Clients
</h3>
<div class="abs client-row">
  <div class="client"><span class="dot"></span>Hartwell's Wine</div>
  <div class="client"><span class="dot"></span>Vesper Wines</div>
  <div class="client"><span class="sq"></span>Ledger Wine Club</div>
</div>

<div class="abs h-rule" style="top:905px"></div>

<h3 class="abs section-title" style="left:502px;top:925px">
  <svg width="19" height="19" viewBox="0 0 19 19"><rect x="0.5" y="2.5" width="18" height="16" fill="none" stroke="#8c0046"/><rect x="0" y="2" width="19" height="4" fill="#8c0046"/><path d="M0 10H19M0 14H19M5 6V19M10 6V19M14.5 6V19" stroke="#8c0046"/></svg>
  Events
</h3>
<svg class="abs" style="left:481px;top:994px" width="12" height="26" viewBox="0 0 12 26"><polyline points="11,1 1,13 11,25" fill="none" stroke="#ccc"/></svg>
<div class="abs event-photo" style="left:503px;background:linear-gradient(180deg,#8a6a48,#c7a274 50%,#5a4634)" role="img" aria-label="Guests gathered at a company gallery event"></div>
<div class="abs event-photo" style="left:650px;background:linear-gradient(180deg,#9c9c9c,#cfcfcf 50%,#707070)" role="img" aria-label="Boardroom set for a company meeting"></div>
<svg class="abs" style="left:802px;top:994px" width="12" height="26" viewBox="0 0 12 26"><polyline points="1,1 11,13 1,25" fill="none" stroke="#ccc"/></svg>

<footer class="abs site-footer">
  <nav class="footer-nav"><a>Home</a><a>About us</a><a>Clients</a><a>Services</a><a>Careers</a><a>Contact us</a></nav>
  <div class="copyright">Copyright Bluefern Business Services Private Limited.</div>
</footer>

</body>
</html>
```